Brightwave Reach - Business Card

We need a business card for a Social Media Marketing company that specializes in online marketing for small businesses in Canada using common Social Media platforms such as Pixlora, Chatterly, Blinkpost & Quibber.

I have uploaded a copy of our logo which I would like utilized in the business card. We would like the business card to be modern yet classy design.

Our website is www.brightwavereach.ca

Industry/Entity Type

Marketing

Contact Information for Business Card

Email: info@brightwavereach.ca
Website: www.brightwavereach.ca
Telephone: 604-555-0193

Colors

Designer to choose colors to be used in the design.

Requirements
Must have
• Social Media icons on reverse
• Please add some designs with color.

```html
<!DOCTYPE html>
<html lang="en">
<head>
<meta charset="utf-8">
<title>Brightwave Reach – Business Card</title>
<link rel="stylesheet" href="https://fonts.googleapis.com/css2?family=Source+Sans+3:wght@400;600;700&display=swap">
<style>
  :root {
    --stage: #3b3430;
    --card: #141414;
    --card-edge: #1c1c1c;
    --ink: #f2f2f2;
    --ink-soft: #c9c9c9;
    --rule: #9a9a9a;
    --accent: #1fb5a8;
    --accent-warm: #f26b3a;
  }
  * { box-sizing: border-box; margin: 0; padding: 0; }
  html, body {
    width: 1200px; height: 864px; overflow: hidden;
    background: var(--stage);
    font-family: "Source Sans 3", "Myriad Pro", Arial, sans-serif;
  }
  .stage { position: relative; width: 1200px; height: 864px; }

  .card {
    position: absolute;
    width: 540px; height: 309px;
    background: var(--card);
    border: 1px solid var(--card-edge);
    border-radius: 3px;
    box-shadow: 0 10px 24px rgba(0,0,0,.45);
    color: var(--ink);
    overflow: hidden;
  }
  .card--front { left: 50px; top: 80px; }
  .card--back  { left: 610px; top: 470px; }

  /* Colour accent band along the card edge */
  .card__accent {
    position: absolute; left: 0; right: 0; bottom: 0; height: 5px;
    background: linear-gradient(90deg, var(--accent), var(--accent-warm));
  }

  /* Brand wordmark */
  .brand {
    display: flex; align-items: center; gap: 10px;
    font-weight: 700; text-transform: uppercase;
    letter-spacing: 1px; line-height: 1; color: var(--ink-soft);
  }
  .brand__square { width: 14px; height: 14px; background: var(--accent); flex: none; }

  /* Front */
  .card--front .brand {
    position: absolute; left: 0; right: 0; top: 70px;
    justify-content: center; font-size: 30px;
  }
  .front__rule {
    position: absolute; left: 40px; right: 40px; top: 158px;
    height: 1px; background: var(--rule);
  }
  .front__rule--base {
    top: 268px; left: 150px; right: 40px;
    background: linear-gradient(90deg, var(--rule), var(--accent));
  }
  .socials {
    position: absolute; left: 50%; top: 148px; transform: translateX(-50%);
    display: flex; gap: 12px; padding: 0 10px;
    background: var(--card); list-style: none;
    font-size: 12px; line-height: 20px; color: var(--ink-soft); white-space: nowrap;
  }
  .socials__item { display: flex; align-items: center; gap: 5px; }
  .socials__dot {
    width: 20px; height: 20px; border-radius: 50%;
    border: 1.5px solid var(--accent);
  }
  .socials__item:nth-child(even) .socials__dot { border-color: var(--accent-warm); }

  /* Back */
  .person { position: absolute; left: 40px; top: 128px; }
  .person__name { font-size: 15px; font-weight: 700; letter-spacing: .3px; line-height: 20px; }
  .person__role { font-size: 14px; color: var(--accent); line-height: 20px; }
  .back__rule {
    position: absolute; left: 40px; width: 250px; top: 172px;
    height: 1px; background: var(--rule);
  }
  .back__rule--base {
    top: 270px; left: 150px; width: 350px;
    background: linear-gradient(90deg, var(--rule), var(--accent-warm));
  }
  .contact { position: absolute; left: 40px; top: 180px; list-style: none; }
  .contact li {
    display: flex; align-items: center; gap: 7px;
    font-size: 13.5px; line-height: 20px; color: var(--ink);
  }
  .contact svg { width: 11px; height: 11px; fill: var(--accent); flex: none; }
  .card--back .brand {
    position: absolute; right: 36px; top: 128px; font-size: 24px; color: var(--ink);
  }
</style>
</head>
<body>
<main class="stage">

  <section class="card card--front" aria-label="Card front">
    <div class="brand"><span class="brand__square"></span>Brightwave Reach</div>
    <div class="front__rule"></div>
    <ul class="socials">
      <li class="socials__item"><span class="socials__dot"></span>Chatterly</li>
      <li class="socials__item"><span class="socials__dot"></span>Pixlora</li>
      <li class="socials__item"><span class="socials__dot"></span>Blinkpost</li>
      <li class="socials__item"><span class="socials__dot"></span>Quibber</li>
    </ul>
    <div class="front__rule front__rule--base"></div>
    <div class="card__accent"></div>
  </section>

  <section class="card card--back" aria-label="Card back">
    <div class="person">
      <p class="person__name">DANIEL MERCER</p>
      <p class="person__role">CEO/FOUNDER</p>
    </div>
    <div class="back__rule"></div>
    <ul class="contact">
      <li>
        <svg viewBox="0 0 12 12" aria-hidden="true"><path d="M2.5 1h2l1 2.5-1.3 1a6 6 0 0 0 3.3 3.3l1-1.3L11 7.5v2A1.5 1.5 0 0 1 9.5 11 8.5 8.5 0 0 1 1 2.5 1.5 1.5 0 0 1 2.5 1z"/></svg>
        604-555-0193
      </li>
      <li>
        <svg viewBox="0 0 12 12" aria-hidden="true"><path d="M1 2.5h10v7H1z M1.6 3 6 6.4 10.4 3" fill="none" stroke="#1fb5a8" stroke-width="1.2"/><path d="M1 2.5h10L6 6.5z"/></svg>
        info@brightwavereach.ca
      </li>
      <li>
        <svg viewBox="0 0 12 12" aria-hidden="true"><path d="M6 .5a4 4 0 0 0-4 4c0 3 4 7 4 7s4-4 4-7a4 4 0 0 0-4-4zm0 5.6a1.6 1.6 0 1 1 0-3.2 1.6 1.6 0 0 1 0 3.2z"/></svg>
        www.brightwavereach.ca
      </li>
    </ul>
    <div class="brand"><span class="brand__square"></span>Brightwave Reach</div>
    <div class="back__rule back__rule--base"></div>
    <div class="card__accent"></div>
  </section>

</main>
</body>
</html>
```